Corvane Capital Business Cards

These are professional business cards that are for my family office.
Put fake emails and phone numbers as of now until I finalize those components. This family office controls my families investments, assets, and future. The cards should be professional.
..
.
.
.
I just uploaded another variation of a logo I would like to see as a business card to I am inbeteen which logo to use

Target Market(s)

business

Industry/Entity Type

business

Contact Information for Business Card

Professional, wealth related, finance related.

Requirements
Must have
• Logo

```html
<!DOCTYPE html>
<html lang="en">
<head>
<meta charset="UTF-8">
<title>Corvane Capital Business Cards</title>
<link href="https://fonts.googleapis.com/css2?family=Playfair+Display:wght@400;500&family=Poppins:wght@400&display=swap" rel="stylesheet">
<style>
  :root {
    --bg: #2b2b2b;
    --gold: #c8b273;
    --gold-deep: #b89f5c;
    --ink: #151515;
    --paper: #ffffff;
    --muted: #3a3a3a;
  }
  * { margin: 0; padding: 0; box-sizing: border-box; }
  html, body { width: 1200px; height: 689px; overflow: hidden; background: var(--bg); }
  .stage {
    width: 1200px; height: 689px;
    display: flex; align-items: center; justify-content: center; gap: 48px;
  }
  .card {
    width: 540px; height: 310px; border-radius: 22px; position: relative; overflow: hidden;
  }
  /* Back side */
  .card--back { background: var(--gold); }
  .back-pattern {
    position: absolute; inset: 0;
    background: linear-gradient(135deg, #cdb879 0%, #c3ab6a 50%, #cbb475 100%);
  }
  .back-mark {
    position: absolute; right: 48px; bottom: 58px;
    font-family: "Playfair Display", serif; font-weight: 400;
    font-size: 17px; letter-spacing: 1px; color: var(--ink); text-transform: uppercase;
  }
  /* Front side */
  .card--front { background: var(--paper); }
  .brand {
    position: absolute; right: 40px; top: 58px;
    font-family: "Playfair Display", serif; font-weight: 400;
    font-size: 34px; letter-spacing: 2px; color: var(--ink); text-transform: uppercase;
  }
  .rule {
    position: absolute; left: 36px; right: 36px; top: 148px;
    height: 1.5px; background: var(--gold);
  }
  .person { position: absolute; left: 40px; top: 96px; }
  .person__name {
    font-family: "Playfair Display", serif; font-size: 21px; letter-spacing: 1px;
    color: var(--ink); text-transform: uppercase;
  }
  .person__name span { color: var(--gold); }
  .person__role {
    font-family: "Poppins", sans-serif; font-size: 14px; color: var(--muted); margin-top: 1px;
  }
  .contacts {
    position: absolute; left: 40px; top: 180px; list-style: none;
    font-family: "Poppins", sans-serif; font-size: 15px; color: var(--ink);
  }
  .contacts li { display: flex; align-items: center; gap: 10px; margin-bottom: 9px; }
  .contacts svg { width: 16px; height: 16px; flex: none; }
  .address {
    position: absolute; right: 40px; top: 184px; text-align: right;
    font-family: "Poppins", sans-serif; font-size: 15px; line-height: 1.45; color: var(--ink);
  }
</style>
</head>
<body>
<main class="stage">
  <section class="card card--back">
    <div class="back-pattern" role="img" aria-label="Repeated embossed company name pattern in tone-on-gold"></div>
    <p class="back-mark">Corvane Capital</p>
  </section>

  <section class="card card--front">
    <p class="brand">Corvane Capital</p>
    <div class="person">
      <p class="person__name">Elliot <span>Marsh</span></p>
      <p class="person__role">Managing Director</p>
    </div>
    <div class="rule"></div>
    <ul class="contacts">
      <li>
        <svg viewBox="0 0 24 24" fill="none" stroke="var(--gold-deep)" stroke-width="2" stroke-linecap="round" stroke-linejoin="round"><path d="M5 3h4l2 5-2.5 1.5a11 11 0 0 0 6 6L16 13l5 2v4a2 2 0 0 1-2 2A17 17 0 0 1 3 5a2 2 0 0 1 2-2z"/></svg>
        044-987 654 321
      </li>
      <li>
        <svg viewBox="0 0 24 24" fill="var(--gold-deep)"><path d="M2 5h20v14H2z"/><path d="M2 5l10 8 10-8" fill="none" stroke="#fff" stroke-width="1.6"/></svg>
        info@corvanemail.com
      </li>
      <li>
        <svg viewBox="0 0 24 24" fill="none" stroke="var(--gold-deep)" stroke-width="1.8"><circle cx="12" cy="12" r="9.5"/><ellipse cx="12" cy="12" rx="4" ry="9.5"/><path d="M2.5 12h19M4 7h16M4 17h16"/></svg>
        www.corvanesite.com
      </li>
    </ul>
    <p class="address">421, Address line goes here<br>45452,Country Name</p>
  </section>
</main>
</body>
</html>
```